cryotherapy business . Whole Body Cryotherapy, Localised Cryotherapy, Cryofacials

Need home page plus services, about, pricing, online booking, contact and blog page

I want something slick, hip and professional. Our studio colours are duck egg blue, white and grey

I would also like a social media scroll at the bottom of every page

I will upload some web designs that I like the look of

Target Market(s)

Men and Women 25-45

Industry/Entity Type

Health And Wellness

Coding

Coded - Design and coding required

Number of Pages Required

5+ page

Font styles to use
Serif
Sans Serif

Requirements
Must have
• Must be eye catching and easy to navigate
Nice to have
• animation
Should not have
• Not sure what the site should not have. I am fairly open to ideas as this is a brand new business.

```html
<!DOCTYPE html>
<html lang="en">
<head>
<meta charset="utf-8">
<title>Frostline – Integrated Cryotherapy Home Page</title>
<link href="https://fonts.googleapis.com/css2?family=Poppins:wght@300;400;500;600;800&display=swap" rel="stylesheet">
<style>
:root{
  --board:#cdf1fb;
  --royal:#0a46a3;
  --royal-deep:#063a8c;
  --duck:#a9ced8;
  --duck-soft:#c6dfe5;
  --ink:#111111;
  --body:#555b63;
  --grey-band:#3d4142;
  --grey-band-2:#4a4e50;
  --footer:#141414;
  --faq:#f1f1f1;
  --white:#ffffff;
}
*{box-sizing:border-box;margin:0;padding:0}
html,body{width:848px;height:1200px;overflow:hidden}
body{background:var(--board);font-family:'Poppins',sans-serif;color:var(--ink);position:relative}
.page{position:absolute;top:34px;width:382px;height:1131px;background:var(--white);overflow:hidden;box-shadow:0 1px 3px rgba(0,0,0,.12)}
.page--a{left:34px}
.page--b{left:433px;top:35px}
.page *{position:absolute}
.page span,.page b,.page i{position:static}

/* top bar */
.topbar{left:0;top:0;width:100%;height:20px;background:#f4f4f4}
.social-row{display:flex;gap:5px;left:26px;top:8px}
.social-row i{display:block;width:4px;height:4px;border-radius:50%;background:#222}
.call{left:236px;top:4px;display:flex;align-items:center;gap:3px;position:absolute}
.call svg{position:static}
.call-text{position:static;font-size:3px;line-height:1.1;color:#333}
.call-text b{display:block;font-size:5.5px;font-weight:600;color:#111}
.book-btn{left:296px;top:4px;width:58px;height:13px;border-radius:7px;background:var(--duck);font-size:4.5px;font-weight:600;color:#0d2a44;display:flex;align-items:center;justify-content:center}

/* hero */
.hero{left:0;width:100%;background:linear-gradient(180deg,var(--royal) 0%,#0b4aa8 55%,#3d78c2 78%,#c4d8ee 90%,#fff 100%)}
.page--a .hero{top:20px;height:182px}
.page--b .hero{top:0;height:202px}
.mist{left:0;width:100%;height:70px;background:radial-gradient(ellipse 30% 60% at 20% 60%,rgba(255,255,255,.35),transparent 70%),radial-gradient(ellipse 35% 55% at 70% 55%,rgba(255,255,255,.3),transparent 70%)}
.page--a .mist{top:120px}
.page--b .mist{top:128px}
.logo{font-size:12.5px;font-weight:400;letter-spacing:1.6px;color:#dfe6ee}
.page--a .logo{left:25px;top:25px}
.page--b .logo{left:25px;top:7px}
.nav{display:flex;gap:10px;align-items:center;font-size:4.6px;color:#fff}
.nav span{padding:1px 5px}
.nav .is-current{border:1px solid #fff;border-radius:6px}
.page--a .nav{left:160px;top:30px}
.page--b .nav{left:153px;top:12px}
.nav svg{position:static}
.kicker,.tagline{width:100%;text-align:center;color:#fff;font-weight:400}
.kicker{font-size:5.6px;letter-spacing:1px}
.tagline{font-size:5.8px;letter-spacing:1.8px}
.headline{width:100%;text-align:center;color:#fff;font-weight:300;font-size:56px;letter-spacing:5px;line-height:1}
.page--a .kicker{top:64px;left:-14px}
.page--a .headline{top:74px;left:-14px}
.page--a .tagline{top:135px;left:-14px}
.page--b .kicker{top:46px;left:-6px}
.page--b .headline{top:55px;left:-6px}
.page--b .tagline{top:115px;left:-6px}
.dots{width:6px;right:34px}
.page--a .dots{top:94px}
.page--b .dots{top:94px}
.dots i{display:block;width:3px;height:3px;border-radius:50%;background:#fff;margin:0 auto 3px}
.dots i:first-child{width:6px;height:6px;border:1px solid #fff;background:radial-gradient(#fff 40%,transparent 45%)}

/* about */
.ring{left:268px;top:332px;width:220px;height:220px;border-radius:50%;border:38px solid var(--duck-soft)}
.photo{background:linear-gradient(135deg,#c9d3f2 0%,#8fa2e6 45%,#5c6fd6 70%,#d8dcef 100%)}
.about-photo{left:25px;top:241px;width:121px;height:167px}
.cabin-photo{left:222px;top:381px;width:99px;height:162px;border-radius:40px 40px 30px 30px;background:linear-gradient(90deg,#1c3f9c 0%,#2f58c0 40%,#e8ecf2 60%,#c9ced6 100%)}
.eyebrow{left:167px;top:244px;font-size:7.5px;color:#333}
.h2{font-weight:800;font-size:11px;color:var(--ink);white-space:nowrap}
.about-h{left:167px;top:256px}
.rule{height:1px;background:var(--duck);width:39px}
.about-rule{left:167px;top:275px}
.copy{font-size:4px;line-height:8.1px;color:var(--body);text-align:justify}
.about-copy{left:167px;top:281px;width:154px}
.btn{width:47px;height:14px;border:1px solid #333;border-radius:8px;font-size:4.7px;font-weight:500;display:flex;align-items:center;justify-content:center;color:#222}
.about-btn{left:167px;top:345px}
.why-h{left:25px;top:432px}
.why-copy{left:25px;top:455px;width:158px}
.why-btn{left:26px;top:510px}

/* services */
.services-band{left:0;top:591px;width:100%;height:131px;background:linear-gradient(135deg,var(--grey-band) 0%,var(--grey-band-2) 40%,#333738 70%,var(--grey-band-2) 100%)}
.services-h{width:100%;text-align:center;top:624px;color:#fff}
.services-rule{left:168px;top:643px;width:23px;background:#fff}
.card{top:661px;width:93px;height:117px;background:#111;border:2px solid #111}
.card--light{background:var(--duck);border-color:var(--duck)}
.card .photo{left:0;top:0;width:100%;height:59px}
.card h3{left:4px;top:64px;font-size:6.6px;font-weight:600;color:#fff;white-space:nowrap}
.card--light h3{color:#0f1a22}
.card p{left:4px;top:76px;width:84px;font-size:3.7px;line-height:7.3px;color:#e8e8e8}
.card--light p{color:#304049}
.card .more{left:5px;top:102px;font-size:4.2px;font-weight:500;color:#fff}
.card--light .more{color:#1b2d38}
.card-1{left:46px}.card-2{left:145px}.card-3{left:242px}

/* faq */
.faq-h{width:100%;text-align:center;top:819px}
.faq-rule{left:110px;top:841px;width:34px;background:#222}
.faq{width:142px;height:50px;background:var(--faq);box-shadow:0 1px 2px rgba(0,0,0,.15)}
.faq--open{background:var(--duck)}
.faq h4{left:12px;top:12px;font-size:5px;font-weight:500;color:#1a1a1a}
.faq p{left:12px;top:21px;width:122px;font-size:3.8px;line-height:7.6px;color:#4b5258}
.faq-1{left:45px;top:859px}.faq-2{left:194px;top:859px}
.faq-3{left:45px;top:916px}.faq-4{left:194px;top:916px}

/* footer */
.footer{left:0;top:999px;width:100%;height:132px;background:var(--footer)}
.footer h5{font-size:5px;font-weight:500;color:#fff;top:18px}
.footer .frule{top:27px;height:1px;width:46px;background:#444}
.footer ul{list-style:none;top:35px;font-size:4px;line-height:9.2px;color:#ddd}
.footer li{position:static}
.col-1{left:56px}.col-2{left:122px}.col-3{left:184px}.col-4{left:262px}
.contact-item{font-size:3.8px;line-height:6px;color:#ddd;left:193px;width:60px}
.contact-item span{display:block;color:#999}
.contact-ico{left:184px}
.news-copy{left:262px;top:35px;width:66px;font-size:3.8px;line-height:6.6px;color:#ddd}
.news-field{left:262px;top:57px;width:64px;height:11px;background:#fff;font-size:3.3px;color:#999;padding:3.5px 4px}
.foot-social{left:263px;top:77px;display:flex;gap:6px}
.foot-social i{display:block;width:4px;height:4px;border-radius:50%;background:#fff}
.foot-line{left:46px;top:111px;width:290px;height:1px;background:#2e2e2e}
.copyright{width:100%;text-align:center;top:117px;font-size:5px;color:#aaa}
.copyright b{color:#fff;font-weight:400}
</style>
</head>
<body>

<!-- Version A: with utility bar -->
<section class="page page--a">
  <div class="hero"></div>
  <div class="mist"></div>
  <div class="topbar"></div>
  <div class="social-row"><i></i><i></i><i></i><i></i><i></i></div>
  <div class="call">
    <svg width="11" height="11" viewBox="0 0 24 24"><circle cx="12" cy="12" r="11" fill="none" stroke="#111" stroke-width="1.6"/><path d="M8 6.5l2 2-1.2 1.6c.8 1.8 2.3 3.3 4.1 4.1l1.6-1.2 2 2-1.4 1.8c-4.6-.4-8.4-4.2-8.8-8.8z" fill="#111"/></svg>
    <div class="call-text">Call Us Today<b>555-014-2290</b></div>
  </div>
  <div class="book-btn">Online Booking</div>
  <div class="logo">FROSTLINE</div>
  <nav class="nav"><span>Home</span><span>Services</span><span>About</span><span>Pricing</span><span>Online Booking</span><span>Contact &amp; Blog</span>
    <svg width="5" height="5" viewBox="0 0 10 10"><circle cx="4" cy="4" r="3" fill="none" stroke="#fff" stroke-width="1.5"/><path d="M6.3 6.3L9 9" stroke="#fff" stroke-width="1.6"/></svg></nav>
  <div class="kicker">THE POWER OF</div>
  <div class="headline">COLD</div>
  <div class="tagline">INTEGRATED CRYOTHERAPY</div>
  <div class="dots"><i></i><i></i><i></i></div>

  <div class="ring"></div>
  <div class="photo about-photo" role="img" aria-label="Client in a robe stepping into a cryotherapy cabin with an attendant"></div>
  <div class="eyebrow">About Us</div>
  <h2 class="h2 about-h">What Is Cryotherapy?</h2>
  <div class="rule about-rule"></div>
  <p class="copy about-copy">Originally invented by doctors as a powerful anti-inflammatory tool, cryotherapy is a quick, noninvasive process that exposes your body to extreme cold of up to -250°F. This sudden drop in temperature increases circulation and pumps reoxygenated and nutrient enriched blood back into the bloodstream reducing pain &amp; inflammation and alleviating sore muscles. It's also known to release 'feel good' endorphins that help improve sleep, reduce stress, and increase your metabolism</p>
  <div class="btn about-btn">READ MORE</div>
  <div class="cabin-photo" role="img" aria-label="Whole body cryotherapy cabin with touch screen"></div>
  <h2 class="h2 why-h">Why Frostline?</h2>
  <p class="copy why-copy">At Frostline, we believe that cryotherapy is one point on the wellness wheel. Our focus is to integrate cryotherapy into your recovery plan or as part of your health &amp; wellness regiment. Located inside Peak Motion—Riverton's acclaimed physical therapy &amp; wellness center, our goal is to: • Understand your goals &amp; customize a treatment plan • Collaborate, when appropriate</p>
  <div class="btn why-btn">READ MORE</div>

  <div class="services-band"></div>
  <h2 class="h2 services-h">Our Services</h2>
  <div class="rule services-rule"></div>
  <article class="card card-1"><div class="photo" role="img" aria-label="Localised cryotherapy session in a cabin"></div><h3>Localised Cryotherapy</h3><p>Change into a robe/wrap (no jewelry or metal is allowed in the FrostCabin). Socks, slippers &amp; mittens are provided.</p><div class="more">LEARN MORE</div></article>
  <article class="card card-2 card--light"><div class="photo" role="img" aria-label="Client inside a whole body cryotherapy chamber"></div><h3>Whole Body Cryotherapy</h3><p>Once you're in the FrostCabin, you'll remove your robe/wrap. The session will last 2-3 minutes depending</p><div class="more">LEARN MORE</div></article>
  <article class="card card-3"><div class="photo" role="img" aria-label="Cryotherapy cabin in a treatment room"></div><h3>Cryofacials</h3><p>You'll exit the FrostCabin and get dressed. Your body will gradually warm-up, boosting your circulation</p><div class="more">LEARN MORE</div></article>

  <h2 class="h2 faq-h">Frequently Asked Question</h2>
  <div class="rule faq-rule"></div>
  <div class="faq faq-1 faq--open"><h4>01. What is Cryotherapy ?</h4><p>Originally invented in Japan in 1978 by Dr. Hanada for treating inflammation caused by rheumatoid arthritis, Cryotherapy has been used for years</p></div>
  <div class="faq faq-2"><h4>02. How does Cryotherapy Work?</h4><p>Cryotherapy is a quick, noninvasive process that exposes your body, or parts of your body, to extreme cold of up to -250°F through the use of liquid nitrogen.</p></div>
  <div class="faq faq-3"><h4>03. What happens during a session?</h4><p>Check-in: As a first time client, you are asked to provide us with your medical history and sign a waiver.</p></div>
  <div class="faq faq-4"><h4>04. How often should i do Cryotherapy?</h4><p>Lorem ipsum dolor sit amet, consectetur adipiscing elit, sed do eiusmod tempor incididunt ut</p></div>

  <footer class="footer">
    <h5 class="col-1">Quick Links</h5><div class="frule col-1"></div>
    <ul class="col-1"><li>Home</li><li>Services</li><li>About</li><li>Pricing</li><li>Online Booking</li><li>Contact &amp; Blog</li></ul>
    <h5 class="col-2">Support</h5><div class="frule col-2"></div>
    <ul class="col-2"><li>Term of use</li><li>Site Map</li><li>Privacy Policy</li></ul>
    <h5 class="col-3">Contact Info</h5><div class="frule col-3"></div>
    <svg class="contact-ico" style="top:34px" width="5" height="6" viewBox="0 0 10 12"><path d="M5 0a4 4 0 0 0-4 4c0 3 4 8 4 8s4-5 4-8a4 4 0 0 0-4-4z" fill="#fff"/><circle cx="5" cy="4" r="1.5" fill="#141414"/></svg>
    <div class="contact-item" style="top:34px">Address:<span># 10, Sed ut perspiciatis unde omnis iste natus error</span></div>
    <svg class="contact-ico" style="top:62px" width="5" height="5" viewBox="0 0 10 10"><path d="M1 1.5l2-1 1.5 2.5-1.2 1c.6 1.3 1.4 2.1 2.7 2.7l1-1.2L9.5 7l-1 2C4.5 9 1 5.5 1 1.5z" fill="#fff"/></svg>
    <div class="contact-item" style="top:62px">Phone:<span>555-014-2290</span></div>
    <svg class="contact-ico" style="top:82px" width="6" height="4" viewBox="0 0 12 8"><rect width="12" height="8" fill="#fff"/><path d="M0 0l6 4.5L12 0" fill="none" stroke="#141414"/></svg>
    <div class="contact-item" style="top:81px">Email:<span>hello@frostline-studio.com</span></div>
    <h5 class="col-4">Newsletter</h5><div class="frule col-4"></div>
    <p class="news-copy">Lorem ipsum dolor sit amet, consectetur adipiscing elit, sed do eiusmod tempor</p>
    <div class="news-field">Type your Email here</div>
    <div class="foot-social"><i></i><i></i><i></i><i></i><i></i></div>
    <div class="foot-line"></div>
    <div class="copyright">© 2019 <b>Frostline</b> | All Rights Reserved</div>
  </footer>
</section>

<!-- Version B: navigation inside hero -->
<section class="page page--b">
  <div class="hero"></div>
  <div class="mist"></div>
  <div class="logo">FROSTLINE</div>
  <nav class="nav"><span class="is-current">Home</span><span>Services</span><span>About</span><span>Pricing</span><span>Online Booking</span><span>Contact &amp; Blog</span>
    <svg width="5" height="5" viewBox="0 0 10 10"><circle cx="4" cy="4" r="3" fill="none" stroke="#fff" stroke-width="1.5"/><path d="M6.3 6.3L9 9" stroke="#fff" stroke-width="1.6"/></svg></nav>
  <div class="kicker">THE POWER OF</div>
  <div class="headline">COLD</div>
  <div class="tagline">INTEGRATED CRYOTHERAPY</div>
  <div class="dots"><i></i><i></i><i></i></div>

  <div class="ring"></div>
  <div class="photo about-photo" role="img" aria-label="Client in a robe stepping into a cryotherapy cabin with an attendant"></div>
  <div class="eyebrow">About Us</div>
  <h2 class="h2 about-h">What Is Cryotherapy?</h2>
  <div class="rule about-rule"></div>
  <p class="copy about-copy">Originally invented by doctors as a powerful anti-inflammatory tool, cryotherapy is a quick, noninvasive process that exposes your body to extreme cold of up to -250°F. This sudden drop in temperature increases circulation and pumps reoxygenated and nutrient enriched blood back into the bloodstream reducing pain &amp; inflammation and alleviating sore muscles. It's also known to release 'feel good' endorphins that help improve sleep, reduce stress, and increase your metabolism</p>
  <div class="btn about-btn">READ MORE</div>
  <div class="cabin-photo" role="img" aria-label="Whole body cryotherapy cabin with touch screen"></div>
  <h2 class="h2 why-h">Why Frostline?</h2>
  <p class="copy why-copy">At Frostline, we believe that cryotherapy is one point on the wellness wheel. Our focus is to integrate cryotherapy into your recovery plan or as part of your health &amp; wellness regiment. Located inside Peak Motion—Riverton's acclaimed physical therapy &amp; wellness center, our goal is to: • Understand your goals &amp; customize a treatment plan • Collaborate, when appropriate</p>
  <div class="btn why-btn">READ MORE</div>

  <div class="services-band"></div>
  <h2 class="h2 services-h" style="top:620px">Our Services</h2>
  <div class="rule services-rule" style="top:639px"></div>
  <article class="card card-1"><div class="photo" role="img" aria-label="Localised cryotherapy session in a cabin"></div><h3>Localised Cryotherapy</h3><p>Change into a robe/wrap (no jewelry or metal is allowed in the FrostCabin). Socks, slippers &amp; mittens are provided.</p><div class="more">LEARN MORE</div></article>
  <article class="card card-2 card--light"><div class="photo" role="img" aria-label="Client inside a whole body cryotherapy chamber"></div><h3>Whole Body Cryotherapy</h3><p>Once you're in the FrostCabin, you'll remove your robe/wrap. The session will last 2-3 minutes depending</p><div class="more">LEARN MORE</div></article>
  <article class="card card-3"><div class="photo" role="img" aria-label="Cryotherapy cabin in a treatment room"></div><h3>Cryofacials</h3><p>You'll exit the FrostCabin and get dressed. Your body will gradually warm-up, boosting your circulation</p><div class="more">LEARN MORE</div></article>

  <h2 class="h2 faq-h">Frequently Asked Question</h2>
  <div class="rule faq-rule"></div>
  <div class="faq faq-1 faq--open"><h4>01. What is Cryotherapy ?</h4><p>Originally invented in Japan in 1978 by Dr. Hanada for treating inflammation caused by rheumatoid arthritis, Cryotherapy has been used for years</p></div>
  <div class="faq faq-2"><h4>02. How does Cryotherapy Work?</h4><p>Cryotherapy is a quick, noninvasive process that exposes your body, or parts of your body, to extreme cold of up to -250°F through the use of liquid nitrogen.</p></div>
  <div class="faq faq-3"><h4>03. What happens during a session?</h4><p>Check-in: As a first time client, you are asked to provide us with your medical history and sign a waiver.</p></div>
  <div class="faq faq-4"><h4>04. How often should i do Cryotherapy?</h4><p>Lorem ipsum dolor sit amet, consectetur adipiscing elit, sed do eiusmod tempor incididunt ut</p></div>

  <footer class="footer">
    <h5 class="col-1">Quick Links</h5><div class="frule col-1"></div>
    <ul class="col-1"><li>Home</li><li>Services</li><li>About</li><li>Pricing</li><li>Online Booking</li><li>Contact &amp; Blog</li></ul>
    <h5 class="col-2">Support</h5><div class="frule col-2"></div>
    <ul class="col-2"><li>Term of use</li><li>Site Map</li><li>Privacy Policy</li></ul>
    <h5 class="col-3">Contact Info</h5><div class="frule col-3"></div>
    <svg class="contact-ico" style="top:34px" width="5" height="6" viewBox="0 0 10 12"><path d="M5 0a4 4 0 0 0-4 4c0 3 4 8 4 8s4-5 4-8a4 4 0 0 0-4-4z" fill="#fff"/><circle cx="5" cy="4" r="1.5" fill="#141414"/></svg>
    <div class="contact-item" style="top:34px">Address:<span># 10, Sed ut perspiciatis unde omnis iste natus error</span></div>
    <svg class="contact-ico" style="top:62px" width="5" height="5" viewBox="0 0 10 10"><path d="M1 1.5l2-1 1.5 2.5-1.2 1c.6 1.3 1.4 2.1 2.7 2.7l1-1.2L9.5 7l-1 2C4.5 9 1 5.5 1 1.5z" fill="#fff"/></svg>
    <div class="contact-item" style="top:62px">Phone:<span>555-014-2290</span></div>
    <svg class="contact-ico" style="top:82px" width="6" height="4" viewBox="0 0 12 8"><rect width="12" height="8" fill="#fff"/><path d="M0 0l6 4.5L12 0" fill="none" stroke="#141414"/></svg>
    <div class="contact-item" style="top:81px">Email:<span>hello@frostline-studio.com</span></div>
    <h5 class="col-4">Newsletter</h5><div class="frule col-4"></div>
    <p class="news-copy">Lorem ipsum dolor sit amet, consectetur adipiscing elit, sed do eiusmod tempor</p>
    <div class="news-field">Type your Email here</div>
    <div class="foot-social"><i></i><i></i><i></i><i></i><i></i></div>
    <div class="foot-line"></div>
    <div class="copyright">© 2019 <b>Frostline</b> | All Rights Reserved</div>
  </footer>
</section>

</body>
</html>
```